we can communicate on this, but i want to follow the approach we took on Pellew|Marsh & Quinlan but i feel the card front needs the black background and the platinum and gold logo. The back? I am open. we can use the same info from PM&Q. Velmont Arc is an enhanced equity investment fund - basically a very exclusive boutique hedge fund that uses only stock options. very advanced things. hope you are interested

Contact Information for Business Card

Dr. Lewis T. Brennick, CFA
Scientifique de fusée financière
701.555.0143
LTBquant47@mailvantor.com

4718 Willow Creek Bend W.
West Fargo, ND 58078

No web site

Colors

Designer to choose colors to be used in the design.

Requirements
Nice to have
• I tend to prefer the most visible applications of the logo to include logo and name, the logo version with a black background and the gold and platinum components separated by the black. I see this working well for a single side (logo and name - this is card front to me).
• I am fairly open to other treatments on the reverse side with the data. To me, it makes sense to have a different color rendition of the logo on the reverse and it may be a muted black tone on tone or an oversized portion that would have spot UV. Or, the reverse may play with colors and layout
Should not have
• Other colors = no no
• Decorative font

```html
<!DOCTYPE html>
<html lang="en">
<head>
<meta charset="utf-8">
<title>Velmont Arc — Business Cards</title>
<link rel="stylesheet" href="https://fonts.googleapis.com/css2?family=Montserrat:wght@400;500;600&family=Oswald:wght@500&display=swap">
<style>
  :root {
    --stage: #1a1a1b;
    --card: #222223;
    --card-edge: #2b2b2c;
    --gold: #d4a72c;
    --platinum: #c9c9cb;
    --ink-light: #f1f1f1;
  }
  * { box-sizing: border-box; margin: 0; padding: 0; }
  html, body {
    width: 1200px; height: 900px; overflow: hidden;
    background: var(--stage);
    font-family: "Montserrat", sans-serif;
  }
  .stage {
    width: 1200px; height: 900px;
    display: flex; flex-direction: column; align-items: center; justify-content: center;
    gap: 30px;
  }
  .card {
    position: relative;
    width: 720px; height: 411px;
    background: linear-gradient(135deg, var(--card) 0%, var(--card-edge) 100%);
    box-shadow: 0 12px 30px rgba(0,0,0,0.55);
  }
  /* Front */
  .card-front {
    display: flex; flex-direction: column; align-items: center; justify-content: center;
    gap: 22px;
  }
  .brand-mark {
    width: 96px; height: 96px; border-radius: 50%;
    background: linear-gradient(135deg, #8a8a8c 0%, var(--platinum) 60%, #e6e6e7 100%);
  }
  .brand-name {
    font-weight: 500; font-size: 40px; letter-spacing: 5px;
    color: var(--platinum); text-transform: uppercase;
  }
  /* Back */
  .card-back { color: var(--ink-light); }
  .identity {
    position: absolute; left: 28px; top: 150px; width: 352px;
    text-align: right; white-space: nowrap;
  }
  .person-name {
    font-family: "Oswald", sans-serif; font-weight: 500;
    font-size: 28px; line-height: 1.1; color: var(--gold); text-transform: uppercase;
  }
  .person-role { font-size: 14px; letter-spacing: 1px; margin-top: 8px; }
  .divider {
    position: absolute; left: 396px; top: 150px;
    width: 2px; height: 62px; background: var(--gold);
  }
  .contacts {
    position: absolute; left: 414px; top: 154px;
    list-style: none; font-size: 15px; letter-spacing: 0.5px; line-height: 27px;
    white-space: nowrap;
  }
  .contacts li { display: flex; align-items: center; gap: 10px; }
  .contacts svg { width: 14px; height: 14px; flex: none; }
  .address {
    position: absolute; left: 0; right: 0; bottom: 56px;
    text-align: center; font-size: 18px; letter-spacing: 1.2px; white-space: nowrap;
  }
</style>
</head>
<body>
<main class="stage">
  <section class="card card-front" aria-label="Card front">
    <div class="brand-mark" aria-hidden="true"></div>
    <div class="brand-name">Velmont Arc</div>
  </section>

  <section class="card card-back" aria-label="Card back">
    <div class="identity">
      <div class="person-name">Dr. Lewis T. Brennick, CFA</div>
      <div class="person-role">Scientifique de fusée financière</div>
    </div>
    <div class="divider"></div>
    <ul class="contacts">
      <li>
        <svg viewBox="0 0 14 14" aria-hidden="true"><path d="M3 1 L5 1 L6 4 L4.5 5.5 Q6 8.5 8.5 9.5 L10 8 L13 9 L13 11 Q12 13 10 13 Q2 11 1 3 Q1 1 3 1 Z" fill="none" stroke="#d4a72c" stroke-width="1.3"/></svg>
        701.555.0143
      </li>
      <li>
        <svg viewBox="0 0 14 14" aria-hidden="true"><rect x="1" y="3" width="12" height="8" fill="none" stroke="#d4a72c" stroke-width="1.3"/><path d="M1 3 L7 8 L13 3" fill="none" stroke="#d4a72c" stroke-width="1.3"/></svg>
        LTBquant47@mailvantor.com
      </li>
    </ul>
    <p class="address">4718 Willow Creek Bend W., West Fargo, ND 58078</p>
  </section>
</main>
</body>
</html>
```